we can communicate on this, but i want to follow the approach we took on Pellew|Marsh & Quinlan but i feel the card front needs the black background and the platinum and gold logo. The back? I am open. we can use the same info from PM&Q. Velmont Arc is an enhanced equity investment fund - basically a very exclusive boutique hedge fund that uses only stock options. very advanced things. hope you are interested

Contact Information for Business Card

Dr. Lewis T. Brennick, CFA
Scientifique de fusée financière
701.555.0143
LTBquant47@mailvantor.com

4718 Willow Creek Bend W.
West Fargo, ND 58078

No web site

Colors

Designer to choose colors to be used in the design.

Requirements
Nice to have
• I tend to prefer the most visible applications of the logo to include logo and name, the logo version with a black background and the gold and platinum components separated by the black. I see this working well for a single side (logo and name - this is card front to me).
• I am fairly open to other treatments on the reverse side with the data. To me, it makes sense to have a different color rendition of the logo on the reverse and it may be a muted black tone on tone or an oversized portion that would have spot UV. Or, the reverse may play with colors and layout
Should not have
• Other colors = no no
• Decorative font

```html
<!DOCTYPE html>
<html lang="en">
<head>
<meta charset="utf-8">
<title>Velmont Arc — Business Card</title>
<link rel="stylesheet" href="https://fonts.googleapis.com/css2?family=Montserrat:wght@400;500;700&display=swap">
<style>
  :root {
    --backdrop: #1b1b1d;
    --card: #262729;
    --card-deep: #141415;
    --gold: #d4ad4a;
    --gold-light: #e8c766;
    --ink: #f2f2f2;
    --band-ink: #2a2210;
  }
  * { box-sizing: border-box; margin: 0; padding: 0; }
  html, body { width: 1200px; height: 800px; overflow: hidden; background: var(--backdrop); }
  body { font-family: "Montserrat", sans-serif; position: relative; }

  .card {
    position: absolute;
    width: 540px;
    height: 310px;
    background: var(--card);
    overflow: hidden;
    box-shadow: 0 18px 40px rgba(0,0,0,0.55);
  }
  .card--front { left: 80px; top: 80px; }
  .card--back { left: 580px; top: 410px; }

  .front__decor {
    position: absolute;
    left: 0; top: 0;
    width: 250px; height: 310px;
    background: var(--card-deep);
    border-top-right-radius: 150px;
    border-bottom-right-radius: 40px;
  }

  .wordmark {
    position: absolute;
    display: flex;
    align-items: center;
    gap: 12px;
  }
  .wordmark__dot {
    width: 34px; height: 34px;
    border-radius: 50%;
    background: var(--gold);
    flex: none;
  }
  .wordmark__name {
    color: var(--ink);
    font-weight: 700;
    letter-spacing: 1px;
    text-transform: uppercase;
    white-space: nowrap;
  }
  .card--front .wordmark { left: 282px; top: 136px; }
  .card--front .wordmark__name { font-size: 22px; }
  .card--back .wordmark { left: 28px; top: 140px; gap: 10px; }
  .card--back .wordmark__dot { width: 30px; height: 30px; }
  .card--back .wordmark__name { font-size: 19px; }

  .back__divider {
    position: absolute;
    left: 250px; top: 50px;
    width: 1px; height: 170px;
    background: linear-gradient(to bottom, transparent, var(--gold), transparent);
  }

  .person { position: absolute; left: 270px; top: 58px; }
  .person__name {
    color: var(--ink);
    font-weight: 700;
    font-size: 14px;
    letter-spacing: 0.3px;
    text-transform: uppercase;
    white-space: nowrap;
  }
  .person__title {
    color: var(--gold);
    font-weight: 500;
    font-size: 12px;
    margin-top: 4px;
    white-space: nowrap;
  }

  .contacts { position: absolute; left: 270px; top: 138px; list-style: none; }
  .contacts__item {
    display: flex;
    align-items: center;
    gap: 8px;
    color: var(--ink);
    font-size: 11.5px;
    margin-bottom: 10px;
    white-space: nowrap;
  }
  .contacts__icon { width: 16px; height: 16px; flex: none; }

  .address-band {
    position: absolute;
    left: 0; bottom: 0;
    width: 100%; height: 46px;
    background: linear-gradient(90deg, var(--gold), var(--gold-light) 55%, var(--gold));
    display: flex;
    align-items: center;
    padding-left: 28px;
    color: var(--band-ink);
    font-weight: 500;
    font-size: 13px;
    letter-spacing: 0.3px;
    white-space: nowrap;
  }
</style>
</head>
<body>
  <section class="card card--front" aria-label="Card front">
    <div class="front__decor" role="img" aria-label="Large tone-on-tone brand decoration"></div>
    <div class="wordmark">
      <span class="wordmark__dot"></span>
      <span class="wordmark__name">Velmont Arc</span>
    </div>
  </section>

  <section class="card card--back" aria-label="Card back">
    <div class="wordmark">
      <span class="wordmark__dot"></span>
      <span class="wordmark__name">Velmont Arc</span>
    </div>
    <div class="back__divider"></div>

    <div class="person">
      <p class="person__name">Dr. Lewis T. Brennick, CFA</p>
      <p class="person__title">Scientifique de fusée financière</p>
    </div>

    <ul class="contacts">
      <li class="contacts__item">
        <svg class="contacts__icon" viewBox="0 0 16 16" aria-hidden="true">
          <circle cx="8" cy="8" r="7.5" fill="var(--gold)"/>
          <path d="M5.3 4.3l1.4 1.5-.7 1a5 5 0 0 0 2.6 2.6l1-.7 1.5 1.4-.9 1.4C7.6 11.3 4.7 8.4 4 5.2z" fill="var(--card)"/>
        </svg>
        701.555.0143
      </li>
      <li class="contacts__item">
        <svg class="contacts__icon" viewBox="0 0 16 16" aria-hidden="true">
          <circle cx="8" cy="8" r="7.5" fill="var(--gold)"/>
          <rect x="4" y="5" width="8" height="6" fill="none" stroke="var(--card)" stroke-width="1.2"/>
          <path d="M4 5l4 3.2L12 5" fill="none" stroke="var(--card)" stroke-width="1.2"/>
        </svg>
        LTBquant47@mailvantor.com
      </li>
    </ul>

    <div class="address-band">4718 Willow Creek Bend W., West Fargo, ND 58078</div>
  </section>
</body>
</html>
```